Small environmental consultancy requires basic yet awesome website design by aspiring and cool desig

We are a small environmental consultancy based in Australia, we have set-out a design brief for our website, using a logo we had completed here on Velto Marsh as well. We hope you can help us with a website!

Website must be wordpress friendly - we have reserved hosting with them already!

Number of Pages Required

4 page

Requirements
Must have
• use supplied logo
• wordpress
• follow provided brief

```html
<!DOCTYPE html>
<html lang="en">
<head>
<meta charset="utf-8">
<title>Greenleaf Advisory</title>
<link href="https://fonts.googleapis.com/css2?family=Open+Sans:wght@400;600;700&display=swap" rel="stylesheet">
<style>
:root{
  --green:#9cc63b;
  --green-dark:#7ea52a;
  --ink:#3a3a3a;
  --muted:#8a8a8a;
  --footer:#ededeb;
  --bar:#e2e2df;
  --white:#ffffff;
}
*{box-sizing:border-box;margin:0;padding:0}
html,body{width:707px;height:1200px;overflow:hidden}
body{font-family:"Open Sans",Arial,sans-serif;color:var(--ink);background:var(--white);position:relative}
.site-header{height:62px;display:flex;justify-content:space-between;align-items:center;padding:0 30px 0 34px;background:var(--white)}
.brand{display:flex;align-items:center;gap:6px;font-weight:700;font-size:15px;color:var(--green-dark)}
.brand-dot{width:12px;height:12px;border-radius:50%;background:var(--green)}
.main-nav{display:flex;height:62px;align-items:stretch}
.main-nav a{display:flex;align-items:center;padding:0 12px;font-size:12px;font-weight:600;color:var(--ink);text-decoration:none;letter-spacing:.3px}
.main-nav a.active{background:var(--green);color:var(--white)}
.hero{position:relative;height:295px}
.hero-media{position:absolute;inset:0;background:linear-gradient(180deg,#d9e4ea 0%,#b9cbd6 35%,#8fa5a0 60%,#5f8a3a 80%,#3f6b26 100%)}
.hero-text{position:absolute;left:0;right:0;top:38px;text-align:center;font-size:24px;line-height:30px;font-weight:600;color:var(--white)}
.hero-text .accent{color:var(--green)}
.section-title{text-align:center;font-size:20px;font-weight:700;color:var(--ink)}
.services{padding:28px 34px 0}
.service-grid{display:grid;grid-template-columns:repeat(4,1fr);gap:14px;margin-top:14px}
.service-media{height:56px}
.service-media.one{background:linear-gradient(135deg,#c9a77a,#7d6a52)}
.service-media.two{background:linear-gradient(135deg,#8a6a4a,#c4a77f)}
.service-media.three{background:linear-gradient(135deg,#f0c420,#555)}
.service-media.four{background:linear-gradient(135deg,#6f9a3e,#a9c86e)}
.service-card h3{font-size:10px;line-height:12px;color:var(--green-dark);font-weight:600;margin:6px 0 4px}
.service-card p{font-size:7.5px;line-height:10px;color:var(--muted)}
.peoples{position:absolute;top:592px;left:0;width:707px;height:246px;background:var(--green);padding:24px 26px 0}
.peoples .section-title{color:var(--white)}
.people-grid{display:grid;grid-template-columns:1fr 1fr;gap:20px;margin-top:26px}
.person{display:grid;grid-template-columns:140px 1fr;gap:12px;color:var(--white)}
.person-id{text-align:center}
.person-photo{width:84px;height:84px;border-radius:50%;border:3px solid var(--white);margin:0 auto 6px;background:radial-gradient(circle at 50% 40%,#c9b29b,#6d6a63)}
.person-name{font-size:13px;font-weight:700}
.person-contact{font-size:7px;line-height:10px}
.person-bio{font-size:7.5px;line-height:11px}
.person-bio p+p{margin-top:8px}
.clients{position:absolute;top:906px;left:0;width:707px}
.client-row{display:flex;justify-content:center;gap:20px;align-items:center;margin-top:22px}
.client{display:flex;align-items:center;gap:4px;font-size:9px;font-weight:600;color:#555}
.client-mark{width:12px;height:12px;border-radius:50%;background:#555}
.site-footer{position:absolute;top:1005px;left:0;width:707px;height:157px;background:var(--footer);padding:20px 34px 0;display:grid;grid-template-columns:1fr 1fr 1.2fr 1fr;gap:20px}
.site-footer h4{font-size:9px;color:var(--green-dark);font-weight:700;margin-bottom:8px}
.site-footer li{list-style:none;font-size:8px;line-height:14px;color:var(--muted)}
.social li{display:flex;align-items:center;gap:6px;margin-bottom:4px}
.social-dot{width:12px;height:12px;border-radius:50%;background:var(--green)}
.copyright{position:absolute;top:1162px;left:0;width:707px;height:38px;background:var(--bar);text-align:center;font-size:8px;line-height:38px;color:var(--muted)}
</style>
</head>
<body>
<header class="site-header">
  <div class="brand"><span class="brand-dot"></span>Greenleaf Advisory</div>
  <nav class="main-nav">
    <a class="active" href="#">HOME</a><a href="#">SERVICES</a><a href="#">PEOPLE</a><a href="#">CLIENTS</a><a href="#">CONTACT</a>
  </nav>
</header>

<section class="hero">
  <div class="hero-media" role="img" aria-label="Glass office towers rising above a lush green garden"></div>
  <h1 class="hero-text">We are a<br>small environmental<br>consultancy<br><span class="accent">based in Australia</span></h1>
</section>

<section class="services">
  <h2 class="section-title">Our Services</h2>
  <div class="service-grid">
    <article class="service-card">
      <div class="service-media one" role="img" aria-label="Team reviewing project plans"></div>
      <h3>Project Management</h3>
      <p>We plan, coordinate and deliver environmental projects on time and on budget, keeping clients informed from scoping to close out.</p>
    </article>
    <article class="service-card">
      <div class="service-media two" role="img" aria-label="Soil sampling on a contaminated site"></div>
      <h3>Contaminated Land Assessment &amp; Remediation</h3>
      <p>Site investigations, soil and groundwater sampling and practical remediation plans that return land to safe, productive use.</p>
    </article>
    <article class="service-card">
      <div class="service-media three" role="img" aria-label="Hazard warning sign against the sky"></div>
      <h3>Hazardous Materials and Occupational Hygiene</h3>
      <p>Asbestos and hazardous material surveys, air monitoring and exposure assessments to keep workplaces safe and compliant.</p>
    </article>
    <article class="service-card">
      <div class="service-media four" role="img" aria-label="Green bushland landscape"></div>
      <h3>Natural Environment Assessment and Management Services</h3>
      <p>Flora and fauna surveys, impact assessments and plans that balance development with care for nature.</p>
    </article>
  </div>
</section>

<section class="peoples">
  <h2 class="section-title">Our Peoples</h2>
  <div class="people-grid">
    <article class="person">
      <div class="person-id">
        <div class="person-photo" role="img" aria-label="Portrait photo of Marcus Hollow"></div>
        <div class="person-name">Marcus Hollow</div>
        <div class="person-contact">marcus@greenleafadvisory.example<br>Mobile: 0491 570 110</div>
      </div>
      <div class="person-bio">
        <p>Marcus has more than fifteen years of experience in environmental consulting across government, mining and property sectors throughout Australia.</p>
        <p>He leads site assessments and remediation projects, working closely with clients to find clear and practical outcomes.</p>
      </div>
    </article>
    <article class="person">
      <div class="person-id">
        <div class="person-photo" role="img" aria-label="Portrait photo of Marcus Hollow"></div>
        <div class="person-name">Marcus Hollow</div>
        <div class="person-contact">marcus@greenleafadvisory.example<br>Mobile: 0491 570 110</div>
      </div>
      <div class="person-bio">
        <p>Marcus holds qualifications in environmental science and occupational hygiene and is a registered assessor for hazardous materials.</p>
        <p>Outside the office he volunteers with local landcare groups and bush regeneration programs.</p>
      </div>
    </article>
  </div>
</section>

<section class="clients">
  <h2 class="section-title">Clients</h2>
  <div class="client-row">
    <span class="client">Riverbend</span>
    <span class="client">Kestrel</span>
    <span class="client">Northgate</span>
    <span class="client"><span class="client-mark"></span>Ashford</span>
    <span class="client">Corvale</span>
    <span class="client"><span class="client-mark"></span>Tidemark</span>
    <span class="client">Brightwater</span>
    <span class="client">Alderly</span>
    <span class="client"><span class="client-mark"></span>Halvern</span>
  </div>
</section>

<footer class="site-footer">
  <div><h4>Quick Links</h4><ul><li>Home</li><li>Services</li><li>People</li><li>Clients</li><li>Contact</li></ul></div>
  <div><h4>Other Links</h4><ul><li>Privacy Policy</li><li>Terms &amp; Conditions</li></ul></div>
  <div><h4>Greenleaf Advisory</h4><ul><li>14 Wattle Lane, Redcliffe, Qld, 4020</li><li>PO Box 210, Redcliffe, Qld 4020</li><li>&nbsp;</li><li>hello@greenleafadvisory.example</li></ul></div>
  <div><h4>Connect With Us</h4><ul class="social"><li><span class="social-dot"></span>Friendbook</li><li><span class="social-dot"></span>Chirper</li></ul></div>
</footer>
<div class="copyright">© 2015 Company Name - All Rights Reserved</div>
</body>
</html>
```